High value cover design for an A4 ideation pad.

The product is NOT A BOOK.

It's an A4 ideation pad for professionals, designers and creators who handwrite their ideas. Visualise creators like Milo Varnet, Owen Plaskit and Gregor Lunwick in your mind's eye.

I'm looking for a cover design for the ideation pad. Both front and back.

It should look, feel and convey the following.

--> A handcrafted product experience

--> High value & Elegance

--> Inspiration

Mandatory --> See Uploaded Files --> Files 1, 5 & 6

Target Market(s)

- Designers

-Creative Professionals

- Entrepreneurs

who handwrite their ideas. Visualise creators like Milo Varnet, Owen Plaskit and Gregor Lunwick in your mind's eye.

Industry/Entity Type

Stationary

Font styles to use
Script
Other font styles liked:
• Calligraphy

Colors
fbed22

Requirements
Must have
• Title text - Quiet Kettle Notes

-Text in gold on brown leather background to convey high value for the front cover.

--> High value & Elegance

--> Inspiration

--> Should compel the customers to pick up and own the idea pad
Nice to have
• That's my take but other ideas are welcome
Should not have
• Must not convey

- low value

```html
<!DOCTYPE html>
<html lang="en">
<head>
<meta charset="utf-8">
<title>Quiet Kettle Notes — Ideation Pad Cover</title>
<link rel="stylesheet" href="https://fonts.googleapis.com/css2?family=Poiret+One&display=swap">
<style>
  :root {
    --ink-black: #000000;
    --binding-white: #ffffff;
    --title-yellow: #fbed22;
    --title-shade: rgba(105, 103, 92, 0.8);
    --box-dark: #151515;
    --box-mid: #333333;
    --box-light: #6a6a6a;
    --spark-grey: rgba(200, 200, 200, 0.28);
  }
  * { margin: 0; padding: 0; box-sizing: border-box; }
  html, body {
    width: 927px;
    height: 1200px;
    overflow: hidden;
    background: var(--ink-black);
  }
  .cover {
    position: relative;
    width: 927px;
    height: 1200px;
    background: var(--ink-black);
    overflow: hidden;
  }
  .spiral-binding {
    position: absolute;
    left: 11px;
    top: 4px;
    width: 14px;
    height: 1192px;
    background-image: radial-gradient(circle, var(--binding-white) 4.4px, transparent 5px);
    background-size: 14px 14.4px;
    background-repeat: repeat-y;
  }
  .spark-photo {
    position: absolute;
    left: 300px;
    top: 0;
    width: 420px;
    height: 336px;
    background: radial-gradient(ellipse 55% 70% at 55% 100%, var(--spark-grey) 0%, transparent 70%);
  }
  .cover-photo {
    position: absolute;
    left: 118px;
    top: 336px;
    width: 727px;
    height: 721px;
    background: linear-gradient(140deg,
      var(--box-dark) 0%,
      var(--box-mid) 20%,
      var(--box-light) 42%,
      var(--box-mid) 60%,
      var(--box-dark) 100%);
  }
  .title {
    position: absolute;
    left: 0;
    top: 0;
    width: 927px;
    font-family: "Poiret One", sans-serif;
    font-weight: 400;
    color: var(--title-yellow);
    text-shadow: 8px 5px 0 var(--title-shade);
  }
  .title-line {
    position: absolute;
    white-space: nowrap;
    line-height: 1;
  }
  .title-lead {
    left: 202px;
    top: 532px;
    font-size: 104px;
    letter-spacing: 1px;
  }
  .title-main {
    left: 240px;
    top: 706px;
    font-size: 178px;
    letter-spacing: 0;
    text-transform: uppercase;
  }
</style>
</head>
<body>
  <main class="cover">
    <div class="spiral-binding" aria-hidden="true"></div>
    <div class="spark-photo" role="img" aria-label="Photograph of bright sparks flying upward from the top edge of the box"></div>
    <div class="cover-photo" role="img" aria-label="Photograph of a dark square box lit by a diagonal beam of light"></div>
    <h1 class="title">
      <span class="title-line title-lead">Quiet Kettle</span>
      <span class="title-line title-main">Notes</span>
    </h1>
  </main>
</body>
</html>
```